Heron Loan Partners Business Card

We need a business card design for our mortgage servicing company. In addition to servicing the loans of homeowners, we help homeowners with purchasing their homes and any mortgage refinancing. We would like to see designs that use the colors in the logo attached below (gold-ish yellow and navy blue), and any other design you deem fit! The design should communicate a simpler life with smart mortgages provided by Heron.

```html
<!DOCTYPE html>
<html lang="en">
<head>
<meta charset="utf-8">
<title>Heron Loan Partners Business Card</title>
<link href="https://fonts.googleapis.com/css2?family=Montserrat:wght@400;500;700&display=swap" rel="stylesheet">
<style>
  :root {
    --navy: #2b285e;
    --gold: #e4b640;
    --white: #ffffff;
    --backdrop: #2a2a2a;
  }
  * { margin: 0; padding: 0; box-sizing: border-box; }
  html, body { width: 1200px; height: 960px; overflow: hidden; }
  body {
    background: var(--backdrop);
    font-family: "Montserrat", sans-serif;
    position: relative;
  }
  .card {
    position: absolute;
    left: 250px;
    width: 700px;
    height: 400px;
    border-radius: 26px;
    background: var(--white);
    overflow: hidden;
  }
  .card--front { top: 50px; }
  .card--back { top: 510px; }

  .wordmark {
    display: flex;
    align-items: center;
    gap: 12px;
    color: var(--navy);
    font-weight: 700;
    white-space: nowrap;
  }
  .wordmark__dot {
    border-radius: 50%;
    background: var(--gold);
    flex: none;
  }
  .card--front .wordmark {
    position: absolute;
    left: 50%; top: 50%;
    transform: translate(-50%, -50%);
    font-size: 46px;
  }
  .card--front .wordmark__dot { width: 40px; height: 40px; }
  .card--back .wordmark {
    position: absolute;
    left: 48px; top: 58px;
    font-size: 25px;
  }
  .card--back .wordmark__dot { width: 22px; height: 22px; }

  .wave { position: absolute; inset: 0; }

  .contact {
    position: absolute;
    right: 40px;
    top: 150px;
    text-align: right;
    color: var(--white);
  }
  .contact__name { font-weight: 700; font-size: 20px; letter-spacing: 0.5px; }
  .contact__role { font-size: 15px; margin-top: 2px; }
  .contact__address { font-size: 14px; line-height: 1.35; margin-top: 18px; }
  .contact__list { list-style: none; margin-top: 8px; font-size: 14px; line-height: 1.65; }
  .contact__list li { display: flex; justify-content: flex-end; align-items: center; gap: 10px; }
  .contact__icon { width: 14px; height: 14px; fill: var(--gold); flex: none; }
</style>
</head>
<body>
  <section class="card card--front" aria-label="Card front">
    <div class="wordmark"><span class="wordmark__dot"></span>Heron Loan Partners</div>
  </section>

  <section class="card card--back" aria-label="Card back">
    <svg class="wave" viewBox="0 0 700 400" aria-hidden="true">
      <path d="M0 300 C220 295 330 170 390 100 C440 40 500 10 560 0 L700 0 L700 400 L0 400 Z" fill="var(--navy)"/>
      <path d="M-10 335 C240 328 350 200 415 125 C470 62 560 28 710 8" fill="none" stroke="var(--white)" stroke-width="24"/>
      <path d="M-10 335 C240 328 350 200 415 125 C470 62 560 28 710 8" fill="none" stroke="var(--gold)" stroke-width="14"/>
    </svg>

    <div class="wordmark"><span class="wordmark__dot"></span>Heron Loan Partners</div>

    <div class="contact">
      <p class="contact__name">DARA WELLINGTON</p>
      <p class="contact__role">Owner</p>
      <p class="contact__address">2450 Riverbend Rd, Ste<br>200, Fairhaven, TX 75099</p>
      <ul class="contact__list">
        <li>555.014.2286
          <svg class="contact__icon" viewBox="0 0 16 16"><path d="M3 1h3l1.5 4-2 1.3a9 9 0 0 0 4.2 4.2L11 8.5l4 1.5v3a2 2 0 0 1-2 2A13 13 0 0 1 1 3a2 2 0 0 1 2-2z"/></svg>
        </li>
        <li>info@heronloanpartners.com
          <svg class="contact__icon" viewBox="0 0 16 16"><path d="M1 3h14v10H1z M1 3l7 6 7-6" stroke="#2b285e" stroke-width="1.2"/></svg>
        </li>
        <li>www.heronloanpartners.com
          <svg class="contact__icon" viewBox="0 0 16 16"><circle cx="8" cy="8" r="7"/><path d="M1 8h14M8 1c-3 3-3 11 0 14M8 1c3 3 3 11 0 14" fill="none" stroke="#2b285e" stroke-width="1"/></svg>
        </li>
      </ul>
    </div>
  </section>
</body>
</html>
```